Wordpress Theme for Medical Clinics

** Please view updated Sitemap2.pdf doc to clarify some confusion ***

This is a multiuser WordPress subscription site for medical clinics. Please see attachment for sitemap. Please do not include extra content like social media icons, search bars, or images. If you have questions, please ask for clarification.
The site contains the following pages and sub-pages:

1. Home
2. Our Clinic
2a. Our Clinic > Mission
2b. Our Clinic > Services
2c. Our Clinic > Clinic Policies
2d. Our Clinic > Schedules
3. Our Staff
3a. Our Staff > [Staff member page]
4. Resources
4a. Resources > Patient Health (index)
4b. Resources > Patient Health (index) > [post]
4c. Resources > Links
4d. Resources > Forms
5. Alerts
5a. Alerts > [Alert Page]
6. Contact Us

Includes the Following Pages, Subpages, and Content
1. Home
a. About Us
b. Our Staff
c. Bulletins
d. Accepting New Patients (shown as an alert widget)
e. Links
i. Physician Toolbox
ii. Book an Appointment
f. Clinic Policies
i. Show first 3 policies (e.g. Late Arrivals, Missed Appointments, Fees)
ii. Link to Clinic Policies page
g. Primary widget (displayed on all pages)
i. Hours of operation
ii. Contact Info
1. Tel
2. Fax
3. Email
4. Address
5. Get directions (link to Route Finder)
2. Our Clinic
a. Main Page
i. Clinic Name
ii. Overview
iii. Languages Spoken
iv. Secondary Navigation
1. Mission
2. Services
3. Clinic Policies
4. Schedules (see attachment)
b. Our Clinic > Mission
c. Our Clinic > Services
i. For each service include service TITLE and DESCRIPTION
d. Our Clinic > Clinic Policies
i. For each policy include policy TITLE and DESCRIPTION
ii. Include the following policies in mockup
1. Late arrivals
2. Missed appointments
3. Fees for missed appointments
4. Referrals and follow-ups
5. Services not covered by RDA
6. Information for LTF patients
7. Medical Legal Reports
e. Our Clinic > Schedules
3. Our Staff
a. Main Page
i. Display a list of staff members. Include NAME and DESIGNATION
b. Our Staff > [Staff Name]
i. Include NAME, PICTURE, DESIGNATION, and BIO
4. Resources
a. Resources > Patient Health
i. Main Page
1. Posts (ordered by date)
a. Title
b. Summary
2. Side Navigation
a. Post Categories
ii. Patient Health > [post title]
1. Title
2. Post Category
3. Date
4. Author
5. Summary
6. Body
b. Resources > Links
1. Secondary Navigation - Categories
a. Sample Categories:
i. Local Services
ii. RDA and Drug Coverage
iii. Mental Health Resources
2. Category page
a. Include the following links in the 'Local Services' category
i. Hypertension clinics
ii. Home Care services
iii. Vaccine Clinics
c. Resources > Forms
i. Display a table with form TITLE and CATEGORY
ii. Side Navigation
1. Form Categories
a. Use the following sample Categories
i. Referrals
ii. Insurance
iii. Intake
iv. Discharge
v. Waivers
5. Alerts
a. Main page
i. List of all Alert posts
1. Include post TITLE as a link to the post
ii. Side Navigation
1. Alerts Archive
a. shown as Month + Number of posts
iii. Alerts > [Alert page]
1. Include TITLE, DATE, AUTHOR, BODY
6. Contact Us
a. Map
b. Hours of operation
c. Address
d. Phone number
e. Fax number
e. Fax number
f. Map
g. Email

Design notes:
- fixed width
- responsive (need designs for mobile, tablet, and desktop)
- simple, dark font, white background
- use Font Awesome icons where needed
- user adds own logo

Target Market(s)

Medical Clinics

Industry/Entity Type

Medical

Number of Pages Required

5+ page

Font styles to use
Serif
Sans Serif

Requirements
Must have
• Please keep designs very simple.
• Examples:
• https://www.quolbin.com/install
• http://www.ventrohax.com/company/about-us
• http://brindlequota.org/
• http://www.trosk.com/
Should not have
• Minimal or no use of shadows and gradients

```html
<!DOCTYPE html>
<html lang="en">
<head>
<meta charset="utf-8">
<title>Clinic Name</title>
<link rel="stylesheet" href="https://fonts.googleapis.com/css2?family=Open+Sans:wght@400;600;700;800&display=swap">
<style>
  :root{
    --orange:#f7941d;
    --blue:#2f9fd6;
    --green:#8cbd22;
    --ink:#222;
    --text:#555;
    --muted:#777;
    --panel:#efefef;
    --rule:#e4e4e4;
    --hero-a:#e9edf1;
    --hero-b:#b9c7d6;
  }
  *{box-sizing:border-box;margin:0;padding:0}
  html,body{width:1200px;height:2553px;overflow:hidden;background:#fff}
  body{font-family:"Open Sans",Arial,sans-serif;color:var(--text);position:relative}
  a{text-decoration:none;color:inherit}

  .site-header{position:absolute;left:0;top:0;width:1200px;height:64px;background:#fff}
  .brand{position:absolute;left:72px;top:8px;font-size:37px;font-weight:800;letter-spacing:.5px;color:var(--orange)}
  .brand span{color:var(--blue)}

  .hero{position:absolute;left:0;top:64px;width:1200px;height:442px;background:linear-gradient(180deg,var(--hero-a),var(--hero-b))}
  .hero-arrow{position:absolute;top:198px;width:46px;height:46px;border-radius:50%;background:rgba(30,30,30,.75);display:flex;align-items:center;justify-content:center}
  .hero-arrow.prev{left:75px}
  .hero-arrow.next{left:1075px}

  .side-nav{position:absolute;left:72px;top:548px;width:237px}
  .side-nav .group{border-bottom:1px solid var(--rule);padding:0 0 14px;margin-bottom:14px}
  .side-nav .top{display:block;font-size:16px;font-weight:700;color:var(--ink);text-transform:uppercase;line-height:24px}
  .side-nav .top.active{color:var(--orange)}
  .side-nav ul{list-style:none;margin-top:4px}
  .side-nav li{font-size:12px;font-weight:700;color:#444;text-transform:uppercase;line-height:26px;padding-left:18px;position:relative}
  .side-nav li::before{content:"";position:absolute;left:4px;top:10px;width:5px;height:5px;border-right:1.5px solid #888;border-top:1.5px solid #888;transform:rotate(45deg)}
  .side-nav li.sub{padding-left:36px}
  .side-nav li.sub::before{left:22px}
  .side-nav .group.last{border:0}

  .widget{position:absolute;top:534px;width:243px;height:370px;background:var(--panel)}
  .widget-head{height:72px;display:flex;align-items:center;gap:12px;padding-left:16px;color:#fff;text-transform:uppercase}
  .widget-head .small{display:block;font-size:14px;font-weight:600;line-height:15px}
  .widget-head .big{display:block;font-size:20px;font-weight:700;line-height:22px}
  .w-new{left:345px}.w-new .widget-head{background:var(--green)}
  .w-hours{left:615px}.w-hours .widget-head{background:var(--blue)}
  .w-contact{left:883px}.w-contact .widget-head{background:var(--orange)}
  .widget-body{padding:16px 18px;font-size:14px}
  .btn-solid{display:inline-block;margin-top:18px;background:var(--orange);color:#fff;font-size:11px;font-weight:700;text-transform:uppercase;padding:11px 22px}
  .hours{width:100%;border-collapse:collapse;font-size:12px}
  .hours td{height:41.5px;vertical-align:middle}
  .hours td:first-child{font-weight:700;color:var(--ink);width:88px}
  .hours td.sep{width:22px}
  .contact-list{font-size:12px}
  .contact-list .row{display:flex;margin-bottom:17px;line-height:19px}
  .contact-list dt{width:102px;font-weight:700;color:var(--ink)}
  .contact-list dd{flex:1}
  .contact-list .link{color:var(--blue)}

  .section-rule{position:absolute;left:345px;width:781px;height:1px;background:var(--rule)}
  .section-title{position:absolute;left:345px;display:flex;align-items:center;gap:12px;font-size:22px;font-weight:700;color:var(--ink);text-transform:uppercase;letter-spacing:.5px}

  .about-text{position:absolute;left:345px;top:996px;width:420px;font-size:16.5px;line-height:29.8px;color:var(--text);hyphens:auto;-webkit-hyphens:auto}
  .about-photo{position:absolute;left:794px;top:1002px;width:332px;height:222px;background:linear-gradient(135deg,#dfe6ea,#9fb0b8)}

  .staff-row{position:absolute;left:345px;width:781px;height:85px;background:var(--panel);display:flex}
  .staff-name{width:179px;background:var(--blue);color:#fff;padding:13px 18px;position:relative}
  .staff-name::after{content:"";position:absolute;right:-9px;top:13px;border-left:9px solid var(--blue);border-top:8px solid transparent;border-bottom:8px solid transparent}
  .staff-name b{display:block;font-size:12px;font-weight:700;text-transform:uppercase}
  .staff-name span{display:block;font-size:12px;margin-top:8px}
  .staff-bio{flex:1;padding:8px 18px 0 22px;font-size:12.5px;line-height:19.5px}
  .staff-bio em{color:#333}

  .btn-outline{position:absolute;left:345px;display:inline-block;border:2px solid var(--orange);color:var(--orange);font-size:11px;font-weight:700;text-transform:uppercase;padding:6px 12px;border-radius:2px}

  .alert-item{position:absolute;left:345px;width:781px;height:108px;border-bottom:1px solid var(--rule)}
  .alert-item svg{position:absolute;left:0;top:0}
  .alert-item h3{position:absolute;left:100px;top:8px;font-size:12.5px;font-weight:700;color:var(--ink);text-transform:uppercase}
  .alert-item p{position:absolute;left:100px;top:30px;width:680px;font-size:13px;line-height:21px;hyphens:auto;-webkit-hyphens:auto}

  .policy-list{position:absolute;left:345px;top:2262px;list-style:none}
  .policy-list li{font-size:14px;text-transform:uppercase;line-height:28px;padding-left:26px;position:relative;color:#444}
  .policy-list li::before{content:"";position:absolute;left:0;top:13px;width:12px;height:1.5px;background:#999}
  .policy-list li::after{content:"";position:absolute;left:6px;top:10px;width:6px;height:6px;border-right:1.5px solid #999;border-top:1.5px solid #999;transform:rotate(45deg)}

  .site-footer{position:absolute;left:345px;top:2475px;width:781px;border-top:1px solid var(--rule);padding-top:16px;font-size:12.5px;line-height:22px;color:#444}
</style>
</head>
<body>
  <header class="site-header">
    <div class="brand">CLINIC <span>NAME</span></div>
  </header>

  <section class="hero" role="img" aria-label="Photo of four smiling clinic doctors and nurses in scrubs and lab coats">
    <a class="hero-arrow prev" href="#" aria-label="Previous slide"><svg width="18" height="18" viewBox="0 0 18 18"><path d="M12 2 5 9l7 7" fill="none" stroke="#fff" stroke-width="3"/></svg></a>
    <a class="hero-arrow next" href="#" aria-label="Next slide"><svg width="18" height="18" viewBox="0 0 18 18"><path d="M6 2l7 7-7 7" fill="none" stroke="#fff" stroke-width="3"/></svg></a>
  </section>

  <nav class="side-nav">
    <div class="group"><a class="top active" href="#">Home</a></div>
    <div class="group">
      <a class="top" href="#">Our Clinic</a>
      <ul><li>Mission</li><li>Services</li><li>Clinic Policies</li><li>Schedules</li></ul>
    </div>
    <div class="group">
      <a class="top" href="#">Our Staff</a>
      <ul><li>Staff Member Page</li></ul>
    </div>
    <div class="group">
      <a class="top" href="#">Resources</a>
      <ul><li>Patient Health</li><li>Patient Health</li><li class="sub">Post</li><li>Links</li><li>Forms</li></ul>
    </div>
    <div class="group">
      <a class="top" href="#">Alerts</a>
      <ul><li>Alert</li></ul>
    </div>
    <div class="group last"><a class="top" href="#">Contact Us</a></div>
  </nav>

  <aside class="widget w-new">
    <div class="widget-head">
      <svg width="34" height="36" viewBox="0 0 34 36"><circle cx="17" cy="10" r="8" fill="#fff"/><path d="M2 36c0-10 6-15 15-15s15 5 15 15z" fill="#fff"/></svg>
      <div><span class="small">New</span><span class="big">Patients</span></div>
    </div>
    <div class="widget-body">
      <p>Accepting new patients</p>
      <a class="btn-solid" href="#">Contact Us</a>
    </div>
  </aside>

  <aside class="widget w-hours">
    <div class="widget-head">
      <svg width="36" height="36" viewBox="0 0 36 36"><circle cx="18" cy="18" r="16" fill="#fff"/><path d="M18 8v11h8" fill="none" stroke="#2f9fd6" stroke-width="3.5"/></svg>
      <div><span class="small">Hours of</span><span class="big">Operation</span></div>
    </div>
    <div class="widget-body" style="padding-top:6px">
      <table class="hours">
        <tr><td>MONDAY</td><td class="sep">:</td><td>8:00am - 6:00pm</td></tr>
        <tr><td>TUESDAY</td><td class="sep">:</td><td>8:00am - 6:00pm</td></tr>
        <tr><td>WEDNESDAY</td><td class="sep">:</td><td>8:00am - 6:00pm</td></tr>
        <tr><td>THURSDAY</td><td class="sep">:</td><td>8:00am - 6:00pm</td></tr>
        <tr><td>FRIDAY</td><td class="sep">:</td><td>8:00am - 6:00pm</td></tr>
        <tr><td>SATURDAY</td><td class="sep">:</td><td>9:00am - 4:00pm</td></tr>
        <tr><td>SUNDAY</td><td class="sep">:</td><td>9:00am - 4:00pm</td></tr>
      </table>
    </div>
  </aside>

  <aside class="widget w-contact">
    <div class="widget-head">
      <svg width="40" height="30" viewBox="0 0 40 30"><rect x="1" y="1" width="38" height="28" rx="3" fill="#fff"/><path d="M3 4l17 13L37 4" fill="none" stroke="#f7941d" stroke-width="3"/></svg>
      <div><span class="small">Contact</span><span class="big">Information</span></div>
    </div>
    <dl class="widget-body contact-list" style="padding-top:20px">
      <div class="row"><dt>TELEPHONE</dt><dd>250 555 0142</dd></div>
      <div class="row"><dt>FAX</dt><dd>250 555 0143</dd></div>
      <div class="row"><dt>EMAIL</dt><dd class="link">hello@clinicbay.co</dd></div>
      <div class="row"><dt>ADDRESS</dt><dd>48 Cedar Lane,<br>Kelowna, B.C.<br>Canada, V1Y2K4</dd></div>
      <div class="row"><dt>DIRECTIONS</dt><dd class="link">Route Finder</dd></div>
    </dl>
  </aside>

  <div class="section-rule" style="top:930px"></div>
  <h2 class="section-title" style="top:951px">
    <svg width="20" height="24" viewBox="0 0 20 24"><rect x="2" y="4" width="16" height="19" rx="1" fill="none" stroke="#222" stroke-width="2.5"/><rect x="6" y="1" width="8" height="5" fill="#222"/><path d="M6 12h8M6 17h8" stroke="#222" stroke-width="2"/></svg>
    About Our Clinic
  </h2>
  <p class="about-text">Lorem Ipsum is simply dummy text of the printing and typesetting industry. Lorem Ipsum has been the industry's standard dummy text ever since the 1500s, when an unknown printer took a galley of type and scrambled it to make a type specimen book. It has survived not only five centuries, but also the leap into electronic typesetdesktop publishing software like Folio Layout Desk including versions of Lorem Ipsum.</p>
  <div class="about-photo" role="img" aria-label="Photo of a bright clinic hallway with glass-walled rooms"></div>

  <div class="section-rule" style="top:1258px"></div>
  <h2 class="section-title" style="top:1283px">
    <svg width="28" height="22" viewBox="0 0 28 22"><circle cx="14" cy="6" r="5" fill="#222"/><circle cx="5" cy="8" r="3.5" fill="#222"/><circle cx="23" cy="8" r="3.5" fill="#222"/><path d="M6 22c0-6 3-10 8-10s8 4 8 10z" fill="#222"/><path d="M0 20c0-5 2-8 5-8s4 2 4 3l-2 5z M28 20c0-5-2-8-5-8s-4 2-4 3l2 5z" fill="#222"/></svg>
    Our Staff
  </h2>

  <article class="staff-row" style="top:1336px"><div class="staff-name"><b>Dr. John Smith, MD</b><span>Physician</span></div><div class="staff-bio">In publishing and graphic design, lorem ipsum is a filler text commonly used to demonstrate the graphic elements of a document or visual presentation.<br><em>[Read more]</em></div></article>
  <article class="staff-row" style="top:1429px"><div class="staff-name"><b>Dr. Jane Doe, MD</b><span>Therapist</span></div><div class="staff-bio">In publishing and graphic design, lorem ipsum is a filler text commonly used to demonstrate the graphic elements of a document or visual presentation.<br><em>[Read more]</em></div></article>
  <article class="staff-row" style="top:1521px"><div class="staff-name"><b>Dr. Willson, MD</b><span>Radiologist</span></div><div class="staff-bio">In publishing and graphic design, lorem ipsum is a filler text commonly used to demonstrate the graphic elements of a document or visual presentation.<br><em>[Read more]</em></div></article>
  <article class="staff-row" style="top:1614px"><div class="staff-name"><b>Dr. John Smith, MD</b><span>Physician</span></div><div class="staff-bio">In publishing and graphic design, lorem ipsum is a filler text commonly used to demonstrate the graphic elements of a document or visual presentation.<br><em>[Read more]</em></div></article>
  <article class="staff-row" style="top:1706px"><div class="staff-name"><b>Dr. John Smith, MD</b><span>Physician</span></div><div class="staff-bio">In publishing and graphic design, lorem ipsum is a filler text commonly used to demonstrate the graphic elements of a document or visual presentation.<br><em>[Read more]</em></div></article>

  <a class="btn-outline" href="#" style="top:1822px">View All Staff</a>

  <div class="section-rule" style="top:1881px"></div>
  <h2 class="section-title" style="top:1907px">
    <svg width="22" height="24" viewBox="0 0 22 24"><path d="M11 1c-5 0-7 4-7 8v6l-3 4h20l-3-4V9c0-4-2-8-7-8z" fill="#222"/><circle cx="11" cy="21" r="3" fill="#222"/></svg>
    Alerts
  </h2>

  <article class="alert-item" style="top:1956px">
    <svg width="72" height="82" viewBox="0 0 72 82"><rect x="3" y="10" width="66" height="69" rx="4" fill="none" stroke="#f7941d" stroke-width="4"/><path d="M3 26h66" stroke="#f7941d" stroke-width="4"/><path d="M18 2v14M54 2v14" stroke="#f7941d" stroke-width="5" stroke-linecap="round"/><text x="36" y="68" text-anchor="middle" font-family="Open Sans,Arial,sans-serif" font-size="32" font-weight="600" fill="#f7941d">23</text></svg>
    <h3>A handy lorem ipsum generator that helps to create dummy text for all layout needs</h3>
    <p>In publishing and graphic design, lorem ipsum is a filler text commonly used to demonstrate the graphic elements of a document or visual presentation.Lorem ipsum dolor sit amet, consectetuer adipiscing elit, sed diam nonummy nibh euismod tincidunt ut laoreet dolore magna aliquam erat volutpat. Ut wisi enim ...</p>
  </article>
  <article class="alert-item" style="top:2081px">
    <svg width="72" height="82" viewBox="0 0 72 82"><rect x="3" y="10" width="66" height="69" rx="4" fill="none" stroke="#f7941d" stroke-width="4"/><path d="M3 26h66" stroke="#f7941d" stroke-width="4"/><path d="M18 2v14M54 2v14" stroke="#f7941d" stroke-width="5" stroke-linecap="round"/><text x="36" y="68" text-anchor="middle" font-family="Open Sans,Arial,sans-serif" font-size="32" font-weight="600" fill="#f7941d">30</text></svg>
    <h3>A handy lorem ipsum generator that helps to create dummy text for all layout needs</h3>
    <p>In publishing and graphic design, lorem ipsum is a filler text commonly used to demonstrate the graphic elements of a document or visual presentation.Lorem ipsum dolor sit amet, consectetuer adipiscing elit, sed diam nonummy nibh euismod tincidunt ut laoreet dolore magna aliquam erat volutpat. Ut wisi enim ...</p>
  </article>

  <h2 class="section-title" style="top:2215px">
    <svg width="20" height="24" viewBox="0 0 20 24"><path d="M1 1h12l6 6v16H1z" fill="#222"/><path d="M13 1v6h6" fill="#fff"/></svg>
    Clinic Policies
  </h2>
  <ul class="policy-list">
    <li>Late Arrivals</li>
    <li>Missed Appointments</li>
    <li>Fees</li>
  </ul>
  <a class="btn-outline" href="#" style="top:2369px">View All Clinic Policies</a>

  <footer class="site-footer">
    <p>©2015 Clinic Name. All Rights Reserved</p>
    <p>Terms &amp; Privacy Policy | Sitemap</p>
  </footer>
</body>
</html>
```